Valmora Company needs a Business Card Design

We just opened our business recently and we need a business card design. Our basic product are clothes and accessories. We would like to see designs that use bright colors like pink, light blue and purple. In addition to that kindly include also our address in the business card which our main office is located in Los Angeles, California.
The final design should communicate that we have affordable price yet high quality brand.

Target Market(s)

young and middle age women

Industry/Entity Type

Business

Contact Information for Business Card

Valmora Apparel and Accessories 4873 North Bellcrest St. Los Angeles California
Tel: 555-318-6492

Logo Text

Valmora's Apparel and Accessories

Font styles to use
Serif

Requirements
Must have
• there should be a graphic of a sexy lady wearing an elegant dress at the upper left corner of the business card.

```html
<!DOCTYPE html>
<html lang="en">
<head>
<meta charset="utf-8">
<title>Valmora Apparel and Accessories – Business Card</title>
<link rel="stylesheet" href="https://fonts.googleapis.com/css2?family=Noto+Serif:wght@400;700&family=Open+Sans:wght@400&display=swap">
<style>
  :root {
    --page-bg: #e9e9e7;
    --ink-black: #000000;
    --wave-line: #ffffff;
    --coral-top: #e85a3f;
    --coral-mid: #f09a86;
    --blush-bottom: #f8dad9;
    --name-white: #ffffff;
    --text-dark: #111111;
    --icon-red: #e0262a;
    --figure-red: #d9262b;
    --figure-pink: #f3c9c4;
  }
  * { margin: 0; padding: 0; box-sizing: border-box; }
  html, body {
    width: 1200px;
    height: 902px;
    overflow: hidden;
    background: var(--page-bg);
  }
  .canvas {
    position: relative;
    width: 1200px;
    height: 902px;
  }
  .business-card {
    position: absolute;
    left: 100px;
    top: 166px;
    width: 1000px;
    height: 570px;
    overflow: hidden;
    background: linear-gradient(180deg, var(--coral-top) 0%, var(--coral-mid) 45%, var(--blush-bottom) 100%);
    box-shadow: 0 6px 24px rgba(0,0,0,0.18);
  }
  .card-wave {
    position: absolute;
    inset: 0;
    width: 1000px;
    height: 570px;
  }
  .brand-name {
    position: absolute;
    left: 134px;
    top: 232px;
    font-family: "Noto Serif", serif;
    font-weight: 700;
    font-size: 62px;
    line-height: 1;
    letter-spacing: 12px;
    color: var(--name-white);
  }
  .brand-tagline {
    position: absolute;
    left: 134px;
    top: 306px;
    font-family: "Noto Serif", serif;
    font-weight: 700;
    font-size: 37px;
    line-height: 1;
    color: var(--text-dark);
  }
  .brand-tagline .joiner {
    font-family: "Open Sans", sans-serif;
    font-weight: 400;
    font-size: 35px;
  }
  .contact-list {
    position: absolute;
    left: 134px;
    top: 448px;
    list-style: none;
    font-family: "Noto Serif", serif;
    font-size: 24px;
    color: var(--text-dark);
  }
  .contact-item {
    display: flex;
    align-items: center;
    gap: 14px;
    height: 34px;
    margin-bottom: 13px;
  }
  .contact-item svg { width: 22px; height: 22px; flex: none; }
  .contact-item.address { font-size: 22px; }
  .figure-area {
    position: absolute;
    left: 793px;
    top: 176px;
    width: 162px;
    height: 364px;
    border-radius: 60px 60px 80px 80px;
    background: linear-gradient(180deg, var(--figure-pink) 0%, var(--figure-red) 30%, var(--figure-red) 100%);
  }
</style>
</head>
<body>
  <main class="canvas">
    <section class="business-card">
      <svg class="card-wave" viewBox="0 0 1000 570" aria-hidden="true">
        <path d="M0 0 H1000 V107 C930 140 870 155 808 152 C700 147 600 92 427 94 C250 96 90 230 0 338 Z" fill="var(--ink-black)"/>
        <path d="M1000 107 C930 140 870 155 808 152 C700 147 600 92 427 94 C250 96 90 230 0 338" fill="none" stroke="var(--wave-line)" stroke-width="6"/>
      </svg>

      <h1 class="brand-name">Valmora</h1>
      <p class="brand-tagline">Apparel <span class="joiner">and</span> Accessories</p>

      <ul class="contact-list">
        <li class="contact-item phone">
          <svg viewBox="0 0 24 24" aria-hidden="true">
            <path fill="var(--icon-red)" d="M6.6 10.8a15.1 15.1 0 0 0 6.6 6.6l2.2-2.2a1 1 0 0 1 1-.25 11.4 11.4 0 0 0 3.6.57 1 1 0 0 1 1 1V20a1 1 0 0 1-1 1A17 17 0 0 1 3 4a1 1 0 0 1 1-1h3.5a1 1 0 0 1 1 1c0 1.25.2 2.45.57 3.57a1 1 0 0 1-.25 1z"/>
          </svg>
          <span>555-318-6492</span>
        </li>
        <li class="contact-item address">
          <svg viewBox="0 0 24 24" aria-hidden="true">
            <path fill="var(--icon-red)" d="M12 2a7 7 0 0 0-7 7c0 5.2 7 13 7 13s7-7.8 7-13a7 7 0 0 0-7-7zm0 9.5A2.5 2.5 0 1 1 12 6.5a2.5 2.5 0 0 1 0 5z"/>
          </svg>
          <span>4873 North Bellcrest St. Los Angeles California</span>
        </li>
      </ul>

      <div class="figure-area" role="img" aria-label="Illustration of a woman in a wide-brimmed hat and a long red evening gown"></div>
    </section>
  </main>
</body>
</html>
```